we need a design for Water Bottle Lable Wrap
The product is called Calmora Springs is a restructured water. its a very healthy and rejuvenating water
we were looking at using as a tag ling Refresh, Renew, Revitalise.

```html
<!DOCTYPE html>
<html lang="en">
<head>
<meta charset="utf-8">
<title>Calmora Springs – Bottle Label Wrap</title>
<link rel="stylesheet" href="https://fonts.googleapis.com/css2?family=Montserrat:wght@400;600&display=swap">
<style>
  :root {
    --page-bg: #ffffff;
    --brand-navy: #2f4e9b;
    --water-pale: #e3f2fc;
    --water-light: #b9def6;
    --water-mid: #6fb4ec;
    --water-deep: #1f4fd6;
    --water-ink: #0f2fb8;
  }
  * { margin: 0; padding: 0; box-sizing: border-box; }
  html, body {
    width: 1200px;
    height: 1200px;
    overflow: hidden;
    background: var(--page-bg);
  }
  .canvas {
    position: relative;
    width: 1200px;
    height: 1200px;
  }
  .label-wrap {
    position: absolute;
    left: 266px;
    top: 100px;
    width: 667px;
    height: 1000px;
    overflow: hidden;
  }
  .label-splash {
    position: absolute;
    inset: 0;
    background:
      radial-gradient(ellipse 45% 70% at 68% 55%, var(--water-mid) 0%, rgba(111,180,236,0) 70%),
      linear-gradient(100deg, var(--water-pale) 0%, var(--water-light) 45%, var(--water-mid) 68%, var(--water-deep) 82%, var(--water-ink) 100%);
  }
  .label-type {
    position: absolute;
    inset: 0;
    width: 667px;
    height: 1000px;
  }
  .brand-name {
    font-family: "Montserrat", sans-serif;
    font-weight: 600;
    font-size: 250px;
    fill: var(--brand-navy);
  }
  .tagline {
    font-family: "Montserrat", sans-serif;
    font-weight: 400;
    font-size: 22px;
    letter-spacing: 2px;
    fill: var(--brand-navy);
  }
</style>
</head>
<body>
  <main class="canvas">
    <section class="label-wrap">
      <div class="label-splash" role="img" aria-label="Photograph of a clear blue water splash rising through the label, deepening to rich blue on the right edge"></div>
      <svg class="label-type" viewBox="0 0 667 1000" xmlns="http://www.w3.org/2000/svg">
        <text class="brand-name" transform="translate(237 892) rotate(-90)" textLength="789" lengthAdjust="spacingAndGlyphs">calmora</text>
        <text class="tagline" transform="translate(300 731) rotate(-90)" textLength="462" lengthAdjust="spacing">REFRESH, RENEW, REVITALISE</text>
      </svg>
    </section>
  </main>
</body>
</html>
```